Onboarding Infographic/brochure

We are a small criminal defense firm looking to create some sort of infographic or brochure that we can onboard new clients with. We are currently sending it out via email but want something a bit cooler and fun to send to clients. The information is:

A Few Quick Rules

We are here to help each step of the way. While questions are never discouraged, this letter will answer some of the most common ones we get asked.

Communications

As a client, you should always be in the loop. While we will try to respond to questions as quickly as possible, sometimes we are unable to respond right away. Do not worry - we promise to get back to you soon. Some questions might take some time to research, and a correct answer is better than a quick one.

Appointments

One of the benefits of having an attorney is the ability to discuss your case outside of court, minus the stress and headaches. If you need an appointment, please contact the office.

Appointments must be scheduled in advance. We do not want you to make a special trip to the office only to learn that we are in court or otherwise unavailable.

Jail Visits

If your family member is currently in jail, we take that very seriously. We will visit your loved one and introduce ourselves. While the case is ongoing, we ask that a family member be designated a “contact” person so that messages can be relayed quickly. Never discuss the facts of the case over the phone with someone who is in jail. Jail calls are recorded and we have seen too many cases go south based on remarks made over recorded lines.

Police Reports and Discovery

We will do our best to provide you with copies of everything we receive on your case. Most information will be emailed, so please keep your email address up to date.

Changes in Contact Information

If you move or change numbers during the case, please let us know. It is difficult to help if we are unable to reach you, and helping you is why we are here.

Court Appearances

Cases do not get resolved as quickly as they do on television. Expect there to be several hearings in your case and it may be necessary for you to attend one or more of them. If a hearing is set, you will receive notice of the date and time of each hearing.

Billing and Collections

We understand that this investment was a huge decision for you. As we focus on providing the best representation, we will need for you to stay on schedule with any payment arrangements agreed to at the time of your initial consultation.

Again, thank you for your trust in us. We look forward to getting a fantastic outcome on your case.

Target Market(s)

Criminal defense clients and their families

Industry/Entity Type

Legal

Font styles to use
Serif

Requirements
Must have
• Must incorporate all of the rules we email out. Would like diagrams, images or pictures
Nice to have
• We attached a Welcome brochure. Not sure I want it to look super similar, hence the request for infographic.

```html
<!DOCTYPE html>
<html lang="en">
<head>
<meta charset="utf-8">
<title>Harbor Legal Group – A Few Quick Rules</title>
<link rel="stylesheet" href="https://fonts.googleapis.com/css2?family=Montserrat:wght@600;700;800&family=Arimo:wght@400;700&display=swap">
<style>
  :root {
    --navy: #1b2a44;
    --navy-deep: #17335e;
    --navy-mid: #1f3a66;
    --blue-change: #1e5aa0;
    --blue-police: #2c7fd6;
    --blue-jail: #3a93e8;
    --blue-appt: #4aa8ef;
    --blue-comm: #80bff2;
    --accent-blue: #5aa2ec;
    --footer-blue: #1a7ad9;
    --orange: #f07c1e;
    --white: #ffffff;
    --logo: #dce8f7;
    --page: #ffffff;
  }
  * { box-sizing: border-box; margin: 0; padding: 0; }
  html, body { width: 1200px; height: 1137px; overflow: hidden; background: var(--page); }
  .sheet {
    position: absolute; left: 52px; top: 146px;
    width: 940px; height: 725px;
    transform: scale(1.1649); transform-origin: 0 0;
    background: var(--navy);
    font-family: "Arimo", Arial, sans-serif;
    color: var(--white);
    box-shadow: 0 1px 4px rgba(0,0,0,.25);
  }
  .abs { position: absolute; }
  .brand { left: 58px; top: 30px; color: var(--logo); font-family: "Montserrat", sans-serif; font-weight: 800; }
  .brand-name { font-size: 52px; letter-spacing: 1px; line-height: 56px; }
  .brand-sub { font-size: 17px; letter-spacing: 11px; line-height: 20px; padding-left: 3px; }
  .headline { left: 403px; top: 34px; font-family: "Montserrat", sans-serif; font-weight: 800; font-size: 40px; letter-spacing: 1px; line-height: 44px; white-space: nowrap; }
  .headline .soft { color: var(--accent-blue); }
  .intro { left: 403px; top: 86px; font-size: 11.5px; font-weight: 700; line-height: 15px; letter-spacing: -0.2px; text-align: center; white-space: nowrap; }
  .wheel { left: 0; top: 0; }
  .rule-title { font-family: "Montserrat", sans-serif; font-weight: 700; font-size: 18.5px; line-height: 21px; letter-spacing: .3px; white-space: nowrap; }
  .rule-body { font-size: 10.2px; line-height: 14px; letter-spacing: -0.05px; }
  .lines { white-space: nowrap; font-size: 10px; line-height: 13.6px; letter-spacing: -0.2px; }
  .dark { color: var(--navy); }
  .just { text-align: justify; }
  .right { text-align: right; }
  .center { text-align: center; }
  .footer { left: 0; top: 669px; width: 940px; height: 56px; }
  .phone { left: 16px; top: 679px; color: var(--blue-change); font-family: "Montserrat", sans-serif; font-weight: 700; font-size: 25px; letter-spacing: .5px; line-height: 36px; white-space: nowrap; }
  .thanks { left: 270px; top: 676px; width: 400px; text-align: center; white-space: nowrap; }
  .thanks-1 { color: #4aa3ff; font-family: "Montserrat", sans-serif; font-weight: 700; font-size: 15.5px; line-height: 19px; }
  .thanks-2 { font-family: "Montserrat", sans-serif; font-weight: 600; font-size: 12px; line-height: 16px; }
  .web { left: 690px; top: 680px; width: 246px; text-align: center; font-family: "Montserrat", sans-serif; font-weight: 700; font-size: 14.5px; line-height: 34px; white-space: nowrap; }
</style>
</head>
<body>
<div class="sheet">

  <div class="abs brand">
    <div class="brand-name">HARBOR</div>
    <div class="brand-sub">LEGAL GROUP</div>
  </div>

  <div class="abs headline"><span class="soft">A FEW</span> QUICK RULES</div>
  <p class="abs intro">We are here to help each step of the way. While questions are never discouraged,<br>this letter will answer some of the most common ones we get asked.</p>

  <svg class="abs wheel" width="940" height="725" viewBox="0 0 940 725">
    <defs>
      <clipPath id="panel-clip"><rect x="48" y="139" width="845" height="508" rx="30"/></clipPath>
      <radialGradient id="photo-tone" cx="45%" cy="40%" r="65%">
        <stop offset="0" stop-color="#8a6a4f"/>
        <stop offset=".55" stop-color="#5d5450"/>
        <stop offset="1" stop-color="#34373d"/>
      </radialGradient>
    </defs>
    <g clip-path="url(#panel-clip)">
      <polygon points="48,139 468,139 468,357 48,286" fill="var(--blue-comm)"/>
      <polygon points="468,139 893,139 893,286 468,357" fill="var(--blue-appt)"/>
      <polygon points="468,357 893,286 893,560" fill="var(--blue-jail)"/>
      <polygon points="468,357 893,560 893,647 673,647" fill="var(--blue-police)"/>
      <polygon points="468,357 673,647 283,647" fill="var(--blue-change)"/>
      <polygon points="468,357 283,647 48,647 48,530" fill="var(--navy-deep)"/>
      <polygon points="468,357 48,530 48,286" fill="var(--navy-mid)"/>
      <g stroke="var(--white)" stroke-width="2.5">
        <line x1="468" y1="357" x2="468" y2="139"/>
        <line x1="468" y1="357" x2="48" y2="286"/>
        <line x1="468" y1="357" x2="48" y2="530"/>
        <line x1="468" y1="357" x2="283" y2="647"/>
        <line x1="468" y1="357" x2="673" y2="647"/>
        <line x1="468" y1="357" x2="893" y2="560"/>
        <line x1="468" y1="357" x2="893" y2="286"/>
      </g>
    </g>
    <rect x="48" y="139" width="845" height="508" rx="30" fill="none" stroke="var(--white)" stroke-width="3"/>

    <circle cx="468" cy="357" r="60" fill="var(--navy-mid)" stroke="var(--white)" stroke-width="3"/>
    <circle cx="468" cy="357" r="52" fill="url(#photo-tone)" stroke="#9fcaf3" stroke-width="2" role="img" aria-label="Photo of a judge's gavel and handcuffs"/>

    <g stroke="var(--white)" stroke-width="3" fill="var(--navy)">
      <circle cx="101" cy="188" r="24"/>
      <circle cx="838" cy="188" r="24"/>
      <circle cx="336" cy="334" r="24"/>
      <circle cx="590" cy="334" r="24"/>
      <circle cx="96" cy="503" r="24"/>
      <circle cx="470" cy="491" r="24"/>
      <circle cx="823" cy="502" r="24"/>
    </g>
    <g fill="none" stroke="var(--orange)" stroke-width="2" stroke-linejoin="round" stroke-linecap="round">
      <path d="M88 177h16v11h-9l-4 4v-4h-3z"/>
      <path d="M107 183h7v10h-3v3l-3-3h-6v-2"/>
      <rect x="826" y="177" width="22" height="20" rx="2"/>
      <line x1="826" y1="183" x2="848" y2="183"/>
      <line x1="831" y1="174" x2="831" y2="179"/><line x1="843" y1="174" x2="843" y2="179"/>
      <circle cx="846" cy="196" r="5" fill="var(--orange)"/>
      <path d="M843.5 196l2 2 3-3.5" stroke="var(--navy)" stroke-width="1.5"/>
      <rect x="325" y="322" width="17" height="23" rx="1"/>
      <line x1="329" y1="328" x2="338" y2="328"/><line x1="329" y1="333" x2="338" y2="333"/><line x1="329" y1="338" x2="334" y2="338"/>
      <path d="M351 331c-1-1.5-5-1.5-5 .5s5 1 5 3.5-4 2-5 .5M348.5 329v10"/>
      <rect x="578" y="324" width="24" height="20"/>
      <line x1="584" y1="324" x2="584" y2="344"/><line x1="590" y1="324" x2="590" y2="344"/><line x1="596" y1="324" x2="596" y2="344"/>
      <line x1="575" y1="324" x2="605" y2="324"/>
      <path d="M84 498l12-7 12 7z"/>
      <line x1="88" y1="501" x2="88" y2="512"/><line x1="94" y1="501" x2="94" y2="512"/><line x1="100" y1="501" x2="100" y2="512"/>
      <line x1="83" y1="515" x2="106" y2="515"/>
      <circle cx="108" cy="510" r="3"/>
      <rect x="457" y="481" width="26" height="19" rx="2"/>
      <circle cx="464" cy="488" r="2.5"/>
      <path d="M460 495c1-3 7-3 8 0"/>
      <line x1="471" y1="487" x2="479" y2="487"/><line x1="471" y1="492" x2="479" y2="492"/>
      <rect x="810" y="491" width="18" height="23" rx="1"/>
      <line x1="814" y1="497" x2="824" y2="497"/><line x1="814" y1="502" x2="824" y2="502"/><line x1="814" y1="507" x2="820" y2="507"/>
      <path d="M832 498l5 2v5c0 4-3 6-5 7-2-1-5-3-5-7v-5z" fill="var(--orange)"/>
    </g>
  </svg>

  <h2 class="abs rule-title dark" style="left:150px;top:166px;">COMMUNICATIONS</h2>
  <p class="abs rule-body dark just" style="left:151px;top:194px;width:299px;">As a client, you should always be in the loop. While we will try to respond to questions as quickly as possible, sometimes we are unable to respond right away. Do not worry - we promise to get back to you soon. Some questions might take some time to research, and a correct answer is better than a quick one.</p>

  <h2 class="abs rule-title dark right" style="left:560px;top:166px;width:225px;">APPOINTMENTS</h2>
  <p class="abs rule-body dark just" style="left:491px;top:194px;width:294px;">One of the benefits of having an attorney is the ability to discuss your case outside of court, minus the stress and headaches. If you need an appointment, please contact the office. Appointments must be scheduled in advance. We do not want you to make a special trip to the office only to learn that we are in court or otherwise unavailable.</p>

  <h2 class="abs rule-title" style="left:71px;top:316px;">BILLING AND<br>COLLECTIONS</h2>
  <p class="abs rule-body just" style="left:71px;top:362px;width:200px;">We understand that this investment was a huge decision for you. As we focus on providing the best representation, we will need for you to stay on schedule with any payment arrangements agreed to at the time of your initial consultation.</p>

  <h2 class="abs rule-title right" style="left:680px;top:308px;width:198px;">JAIL VISITS</h2>
  <p class="abs lines right" style="right:62px;top:334px;">If your family member is currently in jail, we take<br>that very seriously. We will visit your loved one and<br>introduce ourselves. While the case is ongoing, we<br>ask that a family member be designated a “contact”<br>person so that messages can be relayed quickly. Never<br>discuss the facts of the case over the phone with someone<br>who is in jail. Jail calls are recorded and we have seen<br>too many cases go south based on remarks<br>made over recorded lines.</p>

  <h2 class="abs rule-title" style="left:158px;top:502px;">COURT<br>APPEARANCES</h2>
  <p class="abs rule-body just" style="left:68px;top:550px;width:206px;">Cases do not get resolved as quickly as they do on television. Expect there to be several hearings in your case and it may be necessary for you to attend one or more of them. If a hearing is set, you will receive notice of the date and time of each hearing.</p>

  <h2 class="abs rule-title center" style="left:322px;top:543px;width:300px;">CHANGES IN<br>CONTACT INFORMATION</h2>
  <p class="abs rule-body just" style="left:348px;top:590px;width:246px;">If you move or change numbers during the case, please let us know. It is difficult to help if we are unable to reach you, and helping you is why we are here.</p>

  <h2 class="abs rule-title right" style="left:560px;top:528px;width:225px;">POLICE REPORTS<br>&amp; DISCOVERY</h2>
  <p class="abs lines right" style="right:69px;top:577px;">We will do our best to provide you with copies<br>of everything we receive on your case. Most<br>information will be emailed, so please keep<br>your email address up to date.</p>

  <svg class="abs footer" width="940" height="56" viewBox="0 0 940 56">
    <polygon points="0,6 248,6 258,50 0,50" fill="var(--white)"/>
    <polygon points="690,6 940,6 940,50 680,50" fill="var(--footer-blue)"/>
  </svg>
  <div class="abs phone">(555) 014-2290</div>
  <div class="abs thanks">
    <div class="thanks-1">AGAIN, THANK YOU FOR YOUR TRUST IN US.</div>
    <div class="thanks-2">We look forward to getting a fantastic outcome on your case.</div>
  </div>
  <div class="abs web">HARBORLEGALGROUP.COM</div>

</div>
</body>
</html>
```